Business Card Design Project

We have recently completed CraftHive projects for a new logo and wesbite.
We now require new business cards.
We hand out very little printed material to clients as all information is online. When we do hand out something, like a business card, we want it to have real impact and make a statement about the quality and professionalism of our company.
We have an idea of what we want our card to look like but we want a designer to make sure they have impact and look great.
Our requirements are…
Size: 85mm X 55mm - Landscape
Front of card: Logo plus the following contact information.
Dennis Marlow
Operations Manager
Phone +44(0) 1632 xxx xxx
Mobile +44(0) 7700 xxx xxx
Email denmo@korvantix.example
Address 17 Pellick Row, Aberdeen AB12 9QZ
Website www.korvantix.example
How you layout the front of the card is up to you, we would like to see some different ideas. Attached are two versions of our logo that may be used.
Back of card: We would like this to be simple but again have impact. Our current thought is to have the logo or just the large W design from the logo in white against a dark background, perhaps made up from the dark green in the logo.
The logos are attached so you can see the colours in them but the dark ones are..
Dark Blue = C:88, M:55, Y:44, K:28
Dark Green = C:87, M:53, Y:50, K:50
We sometimes also use a bright orange as an accent or highlight colour…
Orange: = C:0, M:39, Y:94, K:0

```html
<!DOCTYPE html>
<html lang="en">
<head>
<meta charset="utf-8">
<title>Korvantix business card concepts</title>
<link rel="stylesheet" href="https://fonts.googleapis.com/css2?family=Open+Sans:wght@400;600;700&display=swap">
<style>
  :root {
    --bg: #efe9e2;
    --card: #ffffff;
    --ink: #1b4650;
    --ink-soft: #3b5f68;
    --teal-dark: #133f46;
    --teal: #5f9aa3;
    --teal-mid: #4f8690;
    --teal-light: #7db0b6;
    --label: #222222;
  }
  * { margin: 0; padding: 0; box-sizing: border-box; }
  html, body { width: 1200px; height: 788px; overflow: hidden; }
  body {
    background: var(--bg);
    font-family: "Open Sans", Arial, sans-serif;
    position: relative;
  }
  .label {
    position: absolute;
    font-size: 21px;
    color: var(--label);
    text-align: center;
    width: 200px;
  }
  .card {
    position: absolute;
    width: 502px;
    height: 325px;
    border-radius: 18px;
    background: var(--card);
    overflow: hidden;
    box-shadow: 0 4px 14px rgba(0,0,0,0.18);
  }
  .card-band { position: absolute; inset: 0; }
  .brand {
    position: absolute;
    display: flex;
    align-items: center;
    gap: 12px;
    color: var(--ink);
    font-weight: 700;
    letter-spacing: 2px;
  }
  .brand-dot {
    border-radius: 50%;
    background: var(--ink);
    flex: none;
  }
  .front .brand { left: 30px; top: 60px; font-size: 34px; }
  .front .brand-dot { width: 26px; height: 26px; }
  .person { position: absolute; left: 30px; top: 168px; color: var(--ink); }
  .person-name { font-size: 17px; font-weight: 700; }
  .person-role { font-size: 12.5px; color: var(--ink-soft); }
  .person-mobile { font-size: 12.5px; margin-top: 6px; }
  .key { font-weight: 700; font-style: italic; margin-right: 4px; }
  .contacts {
    position: absolute;
    right: 14px;
    top: 229px;
    text-align: right;
    color: #ffffff;
    font-size: 12.5px;
    line-height: 21px;
  }
  .back-logo .brand { left: 0; right: 0; justify-content: center; font-size: 46px; }
  .back-1 .brand { top: 112px; }
  .back-3 .brand { top: 170px; }
  .back-logo .brand-dot { width: 34px; height: 34px; }
  .site {
    position: absolute;
    left: 0; right: 0;
    text-align: center;
    color: var(--ink);
    font-size: 18px;
    letter-spacing: 2.5px;
  }
  .back-1 .site { top: 282px; }
  .back-3 .site { top: 278px; }
  .back-2 { background: var(--teal-dark); }
  .back-2 .brand {
    left: 0; right: 0; top: 130px;
    justify-content: center;
    font-size: 52px;
    color: var(--teal);
  }
  .back-2 .brand-dot { width: 40px; height: 40px; background: var(--teal); }
</style>
</head>
<body>
  <div class="label" style="left:220px;top:18px;">Front</div>
  <div class="label" style="left:796px;top:18px;">Back - 1</div>
  <div class="label" style="left:216px;top:402px;">Back - 2</div>
  <div class="label" style="left:796px;top:402px;">Back - 3</div>

  <section class="card front" style="left:85px;top:57px;">
    <svg class="card-band" width="502" height="325" viewBox="0 0 502 325" role="img" aria-label="Decorative wave band in teal tones">
      <defs>
        <linearGradient id="band" x1="0" y1="1" x2="1" y2="0">
          <stop offset="0" stop-color="var(--teal-mid)"/>
          <stop offset="1" stop-color="var(--teal-light)"/>
        </linearGradient>
      </defs>
      <path d="M0 285 C120 292 210 270 280 225 C350 180 420 130 502 118 L502 325 L0 325 Z" fill="url(#band)"/>
    </svg>
    <div class="brand"><span class="brand-dot"></span>KORVANTIX</div>
    <div class="person">
      <div class="person-name">Dennis Marlow</div>
      <div class="person-role">Operations Manager</div>
      <div class="person-mobile"><span class="key">c :</span> +44(0) 7700 xxx xxx</div>
    </div>
    <div class="contacts">
      <div><span class="key">p :</span> +44(0) 1632 xxx xxx</div>
      <div><span class="key">e :</span> denmo@korvantix.example</div>
      <div><span class="key">w :</span> www.korvantix.example</div>
      <div>17 Pellick Row, Aberdeen AB12 9QZ</div>
    </div>
  </section>

  <section class="card back-logo back-1" style="left:626px;top:54px;">
    <div class="brand"><span class="brand-dot"></span>KORVANTIX</div>
    <div class="site">www.korvantix.example</div>
  </section>

  <section class="card back-2" style="left:66px;top:443px;">
    <div class="brand"><span class="brand-dot"></span>KORVANTIX</div>
  </section>

  <section class="card back-logo back-3" style="left:626px;top:444px;">
    <div class="brand"><span class="brand-dot"></span>KORVANTIX</div>
    <div class="site">www.korvantix.example</div>
  </section>
</body>
</html>
```